Website design and coding for new consultancy company

I need to have a full website designed for a new consultancy business I'm trying to establish. It's called BrightPath consult. I need an English version to begin with, and then there should be a Danish version as well, but I'll translate that myself. Just be aware that I need two language versions. The consultancy field that I'm targeting is Leadership - and specialist development. I offer to facilitate corporate academies for global companies as well as specific workshops within leadership- or team development, strategy sessions, personal coaching and facilitation of D&I (Diversity and inclusion) workshops. BTW my logo is not in high resolution - I need that as well.

Target Market(s)

Larger companies that has a need for developing their inhouse leadership capabilities or that wants to develop their specialists to take on more responsibility.

Industry/Entity Type

Consultancy business

Coding

Coded - Design and coding required

Number of Pages Required

5+ page

Requirements
Must have
• Introduction site with a catch phrase. Book a meeting. Services that's beeing offered. Blog site with white papers etc. Language toggle (Danish/English). Cases/testimonials. About site. Contact site.

```html
<!DOCTYPE html>
<html lang="en">
<head>
<meta charset="utf-8">
<title>BrightPath consult – Leadership Development</title>
<link rel="stylesheet" href="https://fonts.googleapis.com/css2?family=Teko:wght@500;600&family=Catamaran:wght@400;500;600;700&display=swap">
<style>
:root{
  --blue:#1f7ac6;
  --blue-light:#7fb8ec;
  --ink:#0b0b0b;
  --text:#3a3f45;
  --muted:#6a7078;
  --white:#ffffff;
  --paper:#f6f8fa;
  --star:#f39a1f;
  --line:#d6d9dd;
}
*{margin:0;padding:0;box-sizing:border-box}
html,body{width:1200px;height:3819px;overflow:hidden;background:var(--white)}
body{position:relative;font-family:"Catamaran",sans-serif;color:var(--text)}
.display{font-family:"Teko",sans-serif;font-weight:600;line-height:1;text-transform:uppercase;letter-spacing:.5px}
.display .accent{color:var(--blue)}
.btn{position:absolute;display:flex;align-items:center;justify-content:center;font-weight:700;font-size:14px;text-transform:uppercase;letter-spacing:.3px}
.btn-blue{background:var(--blue);color:var(--white)}
.btn-black{background:var(--ink);color:var(--white)}

/* header */
.header{position:absolute;left:0;top:0;width:1200px;height:126px;background:var(--white)}
.brand{position:absolute;display:flex;align-items:center;gap:12px;font-family:"Catamaran",sans-serif;font-weight:700;color:var(--ink);white-space:nowrap}
.brand .dot{width:16px;height:16px;background:var(--blue);border-radius:50%;flex:none}
.header .brand{left:104px;top:34px;font-size:34px}
.topbar{position:absolute;left:519px;top:0;width:681px;height:44px;background:var(--blue);clip-path:polygon(0 0,100% 0,100% 100%,26px 100%)}
.topbar .item{position:absolute;top:11px;color:var(--white);font-size:15px;font-weight:600;display:flex;align-items:center;gap:7px;white-space:nowrap}
.lang{position:absolute;left:433px;top:12px;display:flex;align-items:center;gap:6px;font-size:12px;color:var(--text)}
.lang .flag{width:30px;height:30px;border-radius:50%;background:linear-gradient(#b22234 0 50%,#f4f4f4 50%);border:1px solid #ddd}
.socials{position:absolute;display:flex;gap:8px}
.socials span{width:26px;height:26px;border-radius:50%;background:var(--ink);display:block}
.socials.light span{background:var(--white)}
.nav{position:absolute;left:483px;top:78px;display:flex;gap:24px;font-size:14px;font-weight:700;color:var(--ink);white-space:nowrap}
.nav .active{color:var(--blue);font-weight:600}
.header .btn-black{left:948px;top:64px;width:141px;height:45px}

/* hero */
.hero{position:absolute;left:0;top:126px;width:1200px;height:590px;background:
  radial-gradient(circle at 920px 290px,#3f6a9a 0,#1f3e63 120px,transparent 260px),
  radial-gradient(circle at 700px 340px,#5b3a2c 0,transparent 200px),
  linear-gradient(90deg,#07121c 0%,#0c1e2e 40%,#142d46 70%,#0f2236 100%)}
.hero h1{position:absolute;left:108px;top:124px;font-size:66px;color:var(--white);line-height:1.06}
.hero h1 .accent{color:var(--blue-light)}
.hero p{position:absolute;left:111px;top:290px;width:560px;color:var(--white);font-weight:700;font-size:16.5px;line-height:28px;text-transform:uppercase}
.hero .btn{left:113px;top:375px;width:191px;height:45px}

/* about */
.about{position:absolute;left:0;top:716px;width:1200px;height:690px;background:linear-gradient(#f7f9fb,#fff)}
.about .photo{position:absolute;left:111px;top:107px;width:450px;height:470px;background:linear-gradient(160deg,#e9eef3,#b9c7d6 55%,#2c3e58)}
.about .frame{position:absolute;left:444px;top:455px;width:130px;height:130px;border-right:3px solid var(--ink);border-bottom:3px solid var(--ink);border-radius:0 0 4px 0}
.about h2{position:absolute;left:647px;top:120px;font-size:62px;color:var(--ink)}
.about-copy{position:absolute;left:647px;top:213px;width:440px}
.about-copy p{font-size:13.5px;line-height:27.5px;color:var(--muted)}
.about-copy p + p{margin-top:27px}
.about-copy .btn{position:static;margin-top:30px;width:151px;height:44px}

/* services */
.services h2{position:absolute;left:0;top:1460px;width:1200px;text-align:center;font-size:62px;color:var(--ink)}
.services .lead{position:absolute;left:250px;top:1546px;width:700px;text-align:center;font-size:14.5px;line-height:28px;color:var(--muted)}
.card{position:absolute;top:1628px;width:303px}
.card .img{height:322px;position:relative}
.card .img::after{content:"";position:absolute;left:50%;bottom:-18px;margin-left:-18px;border:18px solid transparent;border-bottom:0;border-top-color:#1b2430}
.card h3{margin-top:44px;text-align:center;font-size:16px;font-weight:700;color:var(--ink);text-transform:uppercase}
.glow{position:absolute;left:440px;top:1830px;width:316px;height:280px;border-radius:0 0 160px 160px;background:radial-gradient(circle at 50% 30%,rgba(31,122,198,.18),rgba(31,122,198,.04) 60%,transparent 75%)}
.arrow{position:absolute;font-size:30px;color:var(--ink);font-weight:500}

/* testimonials */
.testimonials{position:absolute;left:0;top:2124px;width:1200px;height:565px;background:radial-gradient(ellipse at 50% 40%,#fbfbfc,#e3e6ea 70%,#d3d8de)}
.testimonials h2{position:absolute;left:0;top:90px;width:1200px;text-align:center;font-size:62px;color:var(--ink)}
.review{position:absolute;top:192px;width:463px;height:287px;background:var(--white)}
.review .name{position:absolute;left:37px;top:52px;color:var(--blue);font-weight:700;font-size:15px;text-transform:uppercase}
.review .badge{position:absolute;left:180px;top:40px;width:36px;height:36px;border-radius:50%;border:5px solid #c9ced4}
.review .source{position:absolute;left:233px;top:36px;font-size:18px;font-weight:600;color:var(--ink)}
.review .stars{position:absolute;left:233px;top:60px;color:var(--star);font-size:17px;letter-spacing:2px}
.review p{position:absolute;left:37px;top:108px;width:390px;font-size:13.5px;line-height:24.5px;color:var(--text)}

/* blog */
.blog h2{position:absolute;left:0;top:2774px;width:1200px;text-align:center;font-size:62px;color:var(--ink)}
.post-main{position:absolute;left:113px;top:2873px;width:448px;height:295px;background:linear-gradient(135deg,#5d5a4c,#2c3a4a 55%,#1c2c44)}
.post-main-title{position:absolute;left:113px;top:3188px;width:460px;font-size:15.5px;line-height:28px;font-weight:700;color:var(--ink);text-transform:uppercase}
.post-thumb{position:absolute;left:577px;width:153px;height:147px}
.post-title{position:absolute;left:756px;width:340px;font-size:15.5px;line-height:27.5px;font-weight:700;color:var(--ink);text-transform:uppercase}
.post-link{position:absolute;left:756px;font-size:15px;font-weight:700;color:var(--blue);text-transform:uppercase}

/* contact band */
.footer-bg{position:absolute;left:0;top:3448px;width:1200px;height:371px;background:var(--ink)}
.touch{position:absolute;left:111px;top:3309px;width:978px;height:251px;background:var(--blue)}
.touch h2{position:absolute;left:44px;top:62px;font-size:62px;color:var(--white)}
.touch p{position:absolute;left:47px;top:136px;width:650px;font-size:13.5px;line-height:24px;color:var(--white)}
.touch .btn{left:797px;top:54px;width:151px;height:45px;font-size:13px}

/* footer */
.footer-line{position:absolute;left:113px;width:978px;height:1px;background:#4a4a4a}
.footer-logo{position:absolute;left:113px;top:3608px;width:234px;height:73px;background:var(--white)}
.footer-logo .brand{left:16px;top:22px;font-size:21px;gap:8px}
.footer-logo .brand .dot{width:12px;height:12px}
.footer-nav{position:absolute;right:110px;top:3636px;display:flex;gap:30px;font-size:14px;font-weight:700;color:var(--white);white-space:nowrap}
.copyright{position:absolute;left:672px;top:3711px;font-size:12.5px;color:var(--white)}
</style>
</head>
<body>

<header class="header">
  <div class="brand"><span class="dot"></span>BrightPath consult</div>
  <div class="lang"><span class="flag" role="img" aria-label="English language flag"></span>EN ⌄</div>
  <div class="socials" style="left:549px;top:8px"><span></span><span></span><span></span></div>
  <div class="topbar">
    <div class="item" style="left:212px">
      <svg width="16" height="12" viewBox="0 0 16 12"><rect x="0.5" y="0.5" width="15" height="11" rx="1.5" fill="none" stroke="#fff"/><path d="M1 1l7 6 7-6" fill="none" stroke="#fff"/></svg>
      info@brightpathconsult.com</div>
    <div class="item" style="left:425px">
      <svg width="13" height="13" viewBox="0 0 24 24"><path fill="#fff" d="M6.6 10.8a15 15 0 0 0 6.6 6.6l2.2-2.2a1 1 0 0 1 1-.25 11.4 11.4 0 0 0 3.6.57 1 1 0 0 1 1 1V20a1 1 0 0 1-1 1A17 17 0 0 1 3 4a1 1 0 0 1 1-1h3.5a1 1 0 0 1 1 1c0 1.25.2 2.45.57 3.6a1 1 0 0 1-.25 1z"/></svg>
      +1 (555) 010 0199</div>
  </div>
  <nav class="nav">
    <span class="active">HOME</span><span>ABOUT US</span><span>SERVICES</span><span>TESTIMONIALS</span><span>INSIGHTS</span>
  </nav>
  <div class="btn btn-black">Contact Us</div>
</header>

<section class="hero" role="img" aria-label="Hand holding a glowing digital globe network in front of a businessman">
  <h1 class="display"><span class="accent">Unlocking Leadership</span><br>Potential Globally</h1>
  <p>Empowering leaders, teams, and organizations through transformative learning experiences.</p>
  <div class="btn btn-blue">Explore Our Services</div>
</section>

<section class="about">
  <div class="photo" role="img" aria-label="Portrait of a consultant in a navy blazer"></div>
  <div class="frame"></div>
  <h2 class="display">About <span class="accent">Us</span></h2>
  <div class="about-copy">
    <p>Lorem ipsum dolor sit amet, consectetur adipiscing elit, sed do eiusmod tempor incididunt ut labore et dolore magna aliqua. Ut enim ad minim veniam, quis nostrud exercitation ullamco laboris nisi ut aliquip ex ea commodo consequat. Duis aute irure dolor in reprehen derit in voluptate velit esse cillum dolore eu fugiat nulla pariatur . Excepteur sint occaecat cupidatat non proident, sunt in culpa qui officia deserunt mollit anim id est laborum.</p>
    <p>Lorem ipsum dolor sit amet, consectetur adipiscing elit, sed do eiusmod tempor incididunt ut labore et dolore</p>
    <div class="btn btn-blue">Learn More</div>
  </div>
</section>

<section class="services">
  <h2 class="display">Our <span class="accent">Services</span></h2>
  <p class="lead">Lorem ipsum dolor sit amet, consectetur adipiscing elit, sed do eiusmod tempor incididunt ut labore et dolore magna aliqua. Ut enim ad minim veniam, quis nostrud exercitation ullamco la</p>
  <div class="glow"></div>
  <div class="arrow" style="left:60px;top:1764px">«</div>
  <div class="arrow" style="left:1117px;top:1764px">»</div>
  <div class="card" style="left:111px">
    <div class="img" role="img" aria-label="Colleagues talking on office stairs" style="background:linear-gradient(135deg,#8a8178,#4d4a48 60%,#2f3138)"></div>
    <h3>Corporate Academies</h3>
  </div>
  <div class="card" style="left:446px">
    <div class="img" role="img" aria-label="Glowing team figures held in open hands" style="background:radial-gradient(circle at 50% 40%,#c8821f,#4a3218 40%,#141414 80%)"></div>
    <h3>Leadership Development</h3>
  </div>
  <div class="card" style="left:782px">
    <div class="img" role="img" aria-label="Business people connected by a network of icons" style="background:linear-gradient(135deg,#b88a55,#6c5a4a 45%,#2f3a48)"></div>
    <h3>Team Development</h3>
  </div>
</section>

<section class="testimonials">
  <h2 class="display">Our <span class="accent">Testimonials</span></h2>
  <div class="arrow" style="left:60px;top:302px">«</div>
  <div class="arrow" style="left:1117px;top:302px">»</div>
  <article class="review" style="left:128px">
    <div class="name">Anna Holm</div><div class="badge"></div>
    <div class="source">Client Reviews</div><div class="stars">★★★★★</div>
    <p>Lorem ipsum dolor sit amet, consectetur adipiscing elit, sed do eiusmod tempor incididunt ut labore et dolore magna aliqua. Ut enim ad minim veniam, quis nostrud exercitation ullamco laboris nisi ut aliquip ex ea commodo consequat. Duis aute irure dolor in reprehenderit in voluptate velit esse cillum dolore eu fugiat nulla pariatur.</p>
  </article>
  <article class="review" style="left:611px">
    <div class="name">Anna Holm</div><div class="badge"></div>
    <div class="source">Client Reviews</div><div class="stars">★★★★★</div>
    <p>Lorem ipsum dolor sit amet, consectetur adipiscing elit, sed do eiusmod tempor incididunt ut labore et dolore magna aliqua. Ut enim ad minim veniam, quis nostrud exercitation ullamco laboris nisi ut aliquip ex ea commodo consequat. Duis aute irure dolor in reprehenderit in voluptate velit esse cillum dolore eu fugiat nulla pariatur.</p>
  </article>
</section>

<section class="blog">
  <h2 class="display">Our <span class="accent">Blog</span></h2>
  <div class="post-main" role="img" aria-label="Smiling senior businessman in an office"></div>
  <div class="post-main-title">Lorem ipsum dolor sit amet, consectetur adipiscing elit, sed do eiusmod tempor incididunt</div>
  <div class="post-thumb" role="img" aria-label="Hands joining puzzle pieces" style="top:2873px;background:linear-gradient(135deg,#3d4550,#c2884a 55%,#5a4638)"></div>
  <div class="post-title" style="top:2884px">Lorem ipsum dolor sit amet, consec tetur adipiscing elit, sed do eiusmod tempor incididunt u</div>
  <div class="post-link" style="top:2983px">Learn More</div>
  <div class="post-thumb" role="img" aria-label="Two colleagues working at a laptop" style="top:3037px;background:linear-gradient(135deg,#e8e6e2,#9a8a7c 55%,#3d4656)"></div>
  <div class="post-title" style="top:3048px">Lorem ipsum dolor sit amet, consec tetur adipiscing elit, sed do eiusmod tempor incididunt u</div>
  <div class="post-link" style="top:3148px">Learn More</div>
</section>

<div class="footer-bg"></div>
<section class="touch">
  <h2 class="display">Get In Touch</h2>
  <p>Lorem ipsum dolor sit amet, consectetur adipiscing elit, sed do eiusmod tempor incididunt ut labore et dolore magna aliqua. Ut enim ad minim veniam, quis nostrud exercitation ullamco laboris nisi ut aliquip ex ea commodo consequat. Duis aute irure dolor in reprehenderit</p>
  <div class="btn btn-black">Email Us</div>
</section>

<footer>
  <div class="footer-line" style="top:3608px"></div>
  <div class="footer-line" style="top:3682px"></div>
  <div class="footer-logo"><div class="brand"><span class="dot"></span>BrightPath consult</div></div>
  <nav class="footer-nav"><span>HOME</span><span>ABOUT US</span><span>SERVICES</span><span>CLIENTS / TESTIMONIALS</span><span>INSIGHTS</span><span>CONTACT US</span></nav>
  <div class="socials light" style="left:205px;top:3706px"><span></span><span></span><span></span></div>
  <div class="copyright">Copyright@2025.All Rights Reserved</div>
</footer>

</body>
</html>
```